Beekeeper needs a label for honey jars

Ciao! I'm from Como Italy
I'm a hobbyist beekeeper and I produce honey for myself and my friends.
I've named my apiary "Dado sereno," a play on words between my nickname (Dado, from Edoardo) and the Italian expression "Dado sereno," which translates to "a drizzle of honey" in English.
I need to create a label for my honey glass jars (250 gr and 500 gr).
I don't need a label for commercial purposes. I would like to include at least the name “Apicoltura Dado sereno", the type of honey (e.g., wildflower, acacia...) and a space for the production year, to be handwritten each year.
In the design some references to the world of bees.
For reference, attached a label with a style I like
Attached are the images of the selected jars and their measurements
Thanks and good job!

Target Market(s)

beekeeping, honey

Requirements
Nice to have
• I would like an elegant style with clean graphics.
Should not have
• Predominance of black color.

```html
<!DOCTYPE html>
<html lang="it">
<head>
<meta charset="utf-8">
<title>Apicoltura Dado sereno – etichetta miele</title>
<link rel="stylesheet" href="https://fonts.googleapis.com/css2?family=Oswald:wght@500;600;700&display=swap">
<style>
  :root {
    --backdrop: #efe9dc;
    --label-white: #ffffff;
    --honey: #e39b2c;
    --honey-soft: #f0c27a;
    --ink-grey: #6d6d6d;
    --ink-dark: #3b3b3b;
    --stitch: #555555;
  }
  * { margin: 0; padding: 0; box-sizing: border-box; }
  html, body {
    width: 1200px; height: 803px; overflow: hidden;
    background: var(--backdrop);
  }
  .label {
    position: relative;
    width: 1200px; height: 803px;
    font-family: "Oswald", "Arial Narrow", sans-serif;
  }
  .label-shape { position: absolute; inset: 0; }
  .label-line {
    position: absolute; left: 0; width: 100%;
    text-align: center; line-height: 1;
  }
  .label-kicker {
    top: 200px; font-size: 36px; font-weight: 600;
    color: var(--ink-grey); letter-spacing: 0.5px;
  }
  .label-name {
    top: 244px; font-size: 72px; font-weight: 700;
    color: var(--honey); letter-spacing: 1px;
  }
  .label-emblem {
    position: absolute; left: 500px; top: 318px;
    width: 200px; height: 160px;
    background: radial-gradient(ellipse at center, var(--honey-soft) 0%, #f7dcae 55%, var(--label-white) 80%);
    border-radius: 50%;
  }
  .label-place {
    top: 516px; font-size: 24px; font-weight: 500;
    color: var(--honey); letter-spacing: 26px; padding-left: 26px;
  }
  .label-place-band {
    position: absolute; left: 527px; top: 546px;
    width: 146px; height: 12px;
    background: linear-gradient(180deg, var(--honey-soft), var(--honey));
    border-radius: 6px;
  }
  .label-variety {
    top: 586px; font-size: 34px; font-weight: 600;
    color: var(--ink-dark); letter-spacing: 0.5px;
  }
  .label-fill {
    top: 652px; font-size: 14px; font-weight: 600;
    color: var(--ink-dark); letter-spacing: 3px;
  }
</style>
</head>
<body>
  <main class="label">
    <svg class="label-shape" width="1200" height="803" viewBox="0 0 1200 803">
      <polygon points="235,401 414,111 786,111 965,401 786,691 414,691" fill="var(--label-white)"/>
      <polygon points="253,401 423,126 777,126 947,401 777,676 423,676"
               fill="none" stroke="var(--stitch)" stroke-width="4" stroke-dasharray="7 7"/>
    </svg>

    <p class="label-line label-kicker">APICOLTURA</p>
    <h1 class="label-line label-name">DADO SERENO</h1>

    <div class="label-emblem" role="img" aria-label="Emblema ape stilizzata con goccia di miele"></div>

    <p class="label-line label-place">COMO</p>
    <div class="label-place-band" role="img" aria-label="Onde del lago stilizzate"></div>

    <p class="label-line label-variety">MILLEFIORI</p>
    <p class="label-line label-fill">....GR | ....</p>
  </main>
</body>
</html>
```